Lorvex Tilo medical cannibis cultivation company

tag - Tilo rise
Lorvex Tilo medical cannabis cultivation - logo is selected- can we please see bold examples with our selection. We are mainly dealing with medical companies and professionals. We would like to be stand out in the crowd with our designs. Welcome any and all attempts. Thanks

Target Market(s)

Medical and Professional

Industry/Entity Type

Medical And Science

Font styles to use
Sans Serif

Colors

Designer to choose colors to be used in the design.

Requirements
Must have
• Bright colour and be bold- Love the teal and magenta that is currently on the dark background design.
Nice to have
• shading and the 3D affect- The shadowed appearance.
Should not have
• Anything related to illegal activity or un professional manners

```html
<!DOCTYPE html>
<html lang="en">
<head>
<meta charset="utf-8">
<title>Lorvex Tilo – Business Cards</title>
<link rel="stylesheet" href="https://fonts.googleapis.com/css2?family=Marcellus&family=Lato:wght@400&display=swap">
<style>
  :root {
    --bg: #d9d3c8;
    --card-light: #ffffff;
    --card-dark: #050505;
    --teal: #12a9e1;
    --magenta: #9a4a9c;
    --grey: #7b7d80;
    --ring: #8d9096;
    --ink: #333333;
  }
  * { margin: 0; padding: 0; box-sizing: border-box; }
  html, body { width: 1200px; height: 1040px; overflow: hidden; background: var(--bg); }
  .canvas { position: relative; width: 1200px; height: 1040px; }

  .card { position: absolute; box-shadow: 0 14px 30px rgba(0,0,0,0.28); }

  .card-front {
    left: 110px; top: 170px; width: 400px; height: 700px;
    background: var(--card-light);
    display: flex; flex-direction: column; align-items: center;
    padding-top: 70px;
  }
  .brand-mark { width: 210px; height: 210px; margin-bottom: 26px; }
  .brand-name {
    font-family: "Marcellus", serif;
    font-size: 50px; letter-spacing: 1px; line-height: 1;
    color: var(--teal);
    white-space: nowrap;
  }
  .tagline {
    display: flex; align-items: center; gap: 10px;
    margin-top: 8px;
    font-family: "Marcellus", serif;
    font-size: 19px; letter-spacing: 4px; text-transform: uppercase;
    color: var(--grey);
  }
  .tagline .rule { width: 58px; height: 2px; background: var(--grey); }

  .person { margin-top: 40px; text-align: center; font-family: "Marcellus", serif; }
  .person-name { font-size: 26px; color: var(--teal); text-transform: uppercase; letter-spacing: 1px; }
  .person-role { font-size: 19px; color: var(--magenta); text-transform: uppercase; margin-top: 2px; }

  .contact {
    margin-top: 22px; text-align: center;
    font-family: "Lato", sans-serif; font-size: 15px; line-height: 1.6; color: var(--ink);
  }
  .contact .web { letter-spacing: 4px; }

  .card-back {
    left: 580px; top: 360px; width: 540px; height: 320px;
    background: var(--card-dark);
    display: flex; align-items: center; justify-content: center; gap: 28px;
  }
  .back-text { display: flex; flex-direction: column; align-items: flex-start; }
  .back-text .brand-name { font-size: 44px; }
  .back-text .tagline { font-size: 16px; color: var(--ring); }
  .back-text .tagline .rule { background: var(--ring); width: 40px; }
  .brand-ring { width: 120px; height: 120px; }
</style>
</head>
<body>
<main class="canvas">
  <section class="card card-front">
    <svg class="brand-mark" viewBox="0 0 210 210" role="img" aria-label="Lorvex Tilo brand mark">
      <circle cx="105" cy="105" r="100" fill="#9a4a9c"/>
    </svg>
    <div class="brand-name">LORVEX TILO</div>
    <div class="tagline"><span class="rule"></span>Tilo rise<span class="rule"></span></div>
    <div class="person">
      <div class="person-name">Dara Venn</div>
      <div class="person-role">CEO/Founder</div>
    </div>
    <div class="contact">
      <div>214 Hollow Fern Road</div>
      <div>Juneau, Alaska 30218</div>
      <div>P. 555 014 2291 E.dara@lorvextilo.com</div>
      <div class="web">www.lorvextilo.com</div>
    </div>
  </section>

  <section class="card card-back">
    <div class="back-text">
      <div class="brand-name">LORVEX TILO</div>
      <div class="tagline"><span class="rule"></span>Tilo rise<span class="rule"></span></div>
    </div>
    <svg class="brand-ring" viewBox="0 0 120 120" aria-hidden="true">
      <circle cx="60" cy="60" r="55" fill="none" stroke="#8d9096" stroke-width="4"/>
    </svg>
  </section>
</main>
</body>
</html>
```